Business Card Design Project - del varosi group

dear Sirs

we need business card design for our group ( DEL Varosi Group ) , i have got the Logo design of our group from pixel harbor in previous , so all need details relating to our group i think available with you, as well as the the chosen logo design

we hope to provide us with business card logo that to be appropaite and satisfactory to us .

thanks

note : logo design of our group is attached .
Updates

Reason: please extend the deadline of my project for additional 15 days because i didn't received appropriate design for our gruop yet . kindly beaware that i have received 77 design till now , supossed to send me 200-250 design at least . thanks

Target Market(s)

contents

name : Kerem EL Nadiri

position : Operation Manager

Industry/Entity Type

Business

Requirements
Must have

• person name

group logo
Nice to have
• logo color matching with back background

```html
<!DOCTYPE html>
<html lang="en">
<head>
<meta charset="utf-8">
<title>DEL Varosi Group – Business Card</title>
<link href="https://fonts.googleapis.com/css2?family=Open+Sans:ital,wght@0,400;0,600;1,400&display=swap" rel="stylesheet">
<style>
  :root {
    --backdrop: #ede4cf;
    --navy: #1d3f8a;
    --navy-deep: #10285e;
    --gold: #d9a93a;
    --gold-light: #f0cf73;
    --ink: #2b2b2b;
    --paper: #ffffff;
  }
  * { box-sizing: border-box; margin: 0; padding: 0; }
  html, body {
    width: 1200px; height: 951px; overflow: hidden;
    background: var(--backdrop);
    font-family: "Open Sans", Arial, sans-serif;
  }
  .canvas { position: relative; width: 1200px; height: 951px; }
  .card {
    position: absolute; width: 600px; height: 340px;
    border-radius: 22px; overflow: hidden;
    box-shadow: 0 6px 18px rgba(0,0,0,0.18);
  }

  /* Front side */
  .card-front {
    left: 90px; top: 80px;
    background: radial-gradient(ellipse at 40% 40%, var(--navy) 0%, var(--navy-deep) 100%);
    display: flex; flex-direction: column; align-items: center; justify-content: center;
  }
  .brand { display: flex; align-items: center; gap: 14px; }
  .brand-mark { width: 22px; height: 22px; }
  .brand-name { font-weight: 600; letter-spacing: 1px; white-space: nowrap; }
  .card-front .brand-mark { background: var(--gold); }
  .card-front .brand-name { color: var(--paper); font-size: 44px; }
  .card-front .website {
    margin-top: 40px; color: var(--gold); font-size: 17px; letter-spacing: 2px;
  }

  /* Back side */
  .card-back { left: 510px; top: 500px; background: var(--paper); }
  .card-back .brand { position: absolute; left: 150px; top: 38px; }
  .card-back .brand-mark { width: 16px; height: 16px; background: var(--gold); }
  .card-back .brand-name { color: var(--navy); font-size: 30px; }
  .person { position: absolute; left: 46px; top: 112px; }
  .person-name { font-size: 20px; color: var(--ink); }
  .person-role { font-size: 15px; color: var(--gold); font-style: italic; }
  .address {
    position: absolute; left: 46px; top: 180px;
    display: flex; gap: 8px; font-size: 15px; line-height: 1.35; color: var(--ink);
  }
  .contacts {
    position: absolute; left: 330px; top: 180px;
    list-style: none; font-size: 15px; line-height: 1.35; color: var(--ink);
  }
  .contacts li { display: flex; align-items: center; gap: 8px; }
  .contacts .accent { color: var(--gold); }
  .icon { width: 14px; height: 14px; flex: none; fill: var(--gold); }
  .address .icon { margin-top: 3px; }
  .swoosh { position: absolute; left: 0; bottom: 0; width: 600px; height: 110px; }
</style>
</head>
<body>
<main class="canvas">

  <section class="card card-front" aria-label="Card front">
    <div class="brand">
      <span class="brand-mark"></span>
      <span class="brand-name">DEL Varosi Group</span>
    </div>
    <p class="website">www.delvarosigroup.com</p>
  </section>

  <section class="card card-back" aria-label="Card back">
    <div class="brand">
      <span class="brand-mark"></span>
      <span class="brand-name">DEL Varosi Group</span>
    </div>

    <div class="person">
      <p class="person-name">Kerem EL Nadiri</p>
      <p class="person-role">Operation Manager</p>
    </div>

    <div class="address">
      <svg class="icon" viewBox="0 0 14 14"><path d="M7 1 L13 6.5 H11 V13 H8.5 V9 H5.5 V13 H3 V6.5 H1 Z"/></svg>
      <p>418 Harlow Ridge Rd.<br>Suite 204-310<br>Brenton, TX 78110</p>
    </div>

    <ul class="contacts">
      <li><svg class="icon" viewBox="0 0 14 14"><path d="M3 1 L5.5 1 L6.5 4 L5 5.2 C5.8 7 7 8.2 8.8 9 L10 7.5 L13 8.5 L13 11 C13 12 12 13 11 13 C5.5 13 1 8.5 1 3 C1 2 2 1 3 1 Z"/></svg>555-014-2200</li>
      <li><svg class="icon" viewBox="0 0 14 14"><path d="M3 1 H10 V5 H3 Z M1 6 H13 V12 H1 Z"/></svg>555-014-2201</li>
      <li><svg class="icon" viewBox="0 0 14 14"><path d="M1 3 H13 V11 H1 Z M1.5 3.5 L7 8 L12.5 3.5" stroke="#fff" stroke-width="1"/></svg>info@<span class="accent">delvarosigroup</span>.com</li>
      <li><svg class="icon" viewBox="0 0 14 14"><circle cx="7" cy="7" r="6"/></svg>www.<span class="accent">delvarosigroup</span>.com</li>
    </ul>

    <svg class="swoosh" viewBox="0 0 600 110" preserveAspectRatio="none" aria-hidden="true">
      <defs>
        <linearGradient id="goldBand" x1="0" x2="1">
          <stop offset="0" stop-color="var(--gold-light)"/>
          <stop offset="1" stop-color="var(--gold)"/>
        </linearGradient>
      </defs>
      <path d="M0 40 C150 90 380 70 600 40 L600 110 L0 110 Z" fill="url(#goldBand)"/>
      <path d="M0 90 C180 100 400 80 600 55 L600 110 L0 110 Z" fill="#1d3f8a"/>
    </svg>
  </section>

</main>
</body>
</html>
```